Business Card Design For A Renovation Contractor Company

We need a business card for a new company based in Singapore, our company name is "RB Tolvane". We are a renovation contractor that builds designs into reality. We build more of F&B restaurants, retail stores and commercial offices. We work very closely with designers. The final design should communicate to our client that we are a company that you can trust, that will plan and complete your project without giving you a headache. I like my client to remember my company as "RB". The beauty of SIMPLE is important.

Industry/Entity Type

Contractor

Requirements
Nice to have
• Black or Red base

```html
<!DOCTYPE html>
<html lang="en">
<head>
<meta charset="utf-8">
<title>RB Tolvane – Business Card</title>
<link href="https://fonts.googleapis.com/css2?family=Questrial&display=swap" rel="stylesheet">
<style>
  :root {
    --bg: #e4e6ea;
    --card: #ffffff;
    --ink: #1a1a1a;
    --black: #0b0b0b;
    --red: #e0161e;
    --white: #ffffff;
    --rule: #555555;
  }
  * { margin: 0; padding: 0; box-sizing: border-box; }
  html, body { width: 1200px; height: 987px; overflow: hidden; }
  body {
    background: var(--bg);
    font-family: "Questrial", "Century Gothic", sans-serif;
    color: var(--ink);
    position: relative;
  }
  .card {
    position: absolute;
    width: 600px;
    height: 343px;
    background: var(--card);
    border-radius: 30px;
    overflow: hidden;
    box-shadow: 0 6px 18px rgba(0,0,0,0.12);
  }
  .card--back { left: 550px; top: 90px; }
  .card--front { left: 50px; top: 520px; }

  .brand {
    position: absolute;
    display: flex;
    flex-direction: column;
    align-items: flex-start;
  }
  .brand__row { display: flex; align-items: center; gap: 14px; }
  .brand__dot {
    width: 34px; height: 34px; border-radius: 50%;
    background: var(--red);
  }
  .brand__name {
    font-size: 50px;
    line-height: 1;
    color: var(--ink);
    letter-spacing: 0.5px;
  }
  .brand__tagline {
    margin-top: 6px;
    padding-top: 4px;
    border-top: 1.5px solid var(--rule);
    font-size: 19px;
    letter-spacing: 0.4px;
    color: var(--ink);
    width: 100%;
    white-space: nowrap;
  }
  .card--back .brand { left: 140px; top: 100px; }
  .website {
    position: absolute;
    left: 0; right: 0; top: 235px;
    text-align: center;
    font-size: 20px;
    letter-spacing: 4px;
    color: var(--ink);
  }
  .website strong { color: var(--red); font-weight: 400; }

  .card--front .brand { left: 190px; top: 40px; }
  .swoosh { position: absolute; inset: 0; }
  .holder {
    position: absolute;
    left: 292px; top: 150px;
    font-size: 22px;
    font-weight: 700;
    color: var(--ink);
  }
  .holder__title { color: var(--red); font-weight: 400; }

  .contacts {
    position: absolute;
    left: 28px; top: 236px;
    color: var(--white);
    font-size: 16px;
    line-height: 1.7;
  }
  .contacts__line { display: flex; align-items: center; gap: 8px; white-space: nowrap; }
  .icon { width: 14px; height: 14px; flex: none; }
  .gap { width: 10px; }
</style>
</head>
<body>

  <section class="card card--back" aria-label="Business card back">
    <div class="brand">
      <div class="brand__row">
        <span class="brand__dot"></span>
        <span class="brand__name">RB Tolvane</span>
      </div>
      <div class="brand__tagline">fit-outs finished to your plan</div>
    </div>
    <p class="website">www.<strong>rbtolvane</strong>.com</p>
  </section>

  <section class="card card--front" aria-label="Business card front">
    <svg class="swoosh" viewBox="0 0 600 343" preserveAspectRatio="none" aria-hidden="true">
      <path d="M0 110 Q 250 215 600 290 L600 343 L0 343 Z" fill="var(--red)"/>
      <path d="M0 122 Q 250 227 600 302 L600 343 L0 343 Z" fill="var(--black)"/>
    </svg>

    <div class="brand">
      <div class="brand__row">
        <span class="brand__dot"></span>
        <span class="brand__name">RB Tolvane</span>
      </div>
      <div class="brand__tagline">fit-outs finished to your plan</div>
    </div>

    <p class="holder">Your Name, <span class="holder__title">Title</span></p>

    <div class="contacts">
      <div class="contacts__line">
        <svg class="icon" viewBox="0 0 16 16"><path d="M4 1l3 3-2 2a9 9 0 0 0 5 5l2-2 3 3-2 3C6 15 1 10 1 3z" fill="#fff"/></svg>
        123-456-0789
        <span class="gap"></span>
        <svg class="icon" viewBox="0 0 16 16"><rect x="4" y="1" width="8" height="14" rx="1.5" fill="#fff"/><rect x="5.5" y="3" width="5" height="7" fill="#000"/></svg>
        123-456-0789
      </div>
      <div class="contacts__line">
        <svg class="icon" viewBox="0 0 16 16"><rect x="1" y="3" width="14" height="10" rx="1" fill="#fff"/><path d="M1.5 3.5 8 9l6.5-5.5" stroke="#000" stroke-width="1.3" fill="none"/></svg>
        info@rbtolvane.com
        <span class="gap"></span>
        <svg class="icon" viewBox="0 0 16 16"><circle cx="8" cy="8" r="7" fill="#fff"/><path d="M1 8h14M8 1c-3 4-3 10 0 14M8 1c3 4 3 10 0 14" stroke="#000" stroke-width="1" fill="none"/></svg>
        www.rbtolvane.com
      </div>
      <div class="contacts__line">Street Name, City Name, State Zip Code</div>
    </div>
  </section>

</body>
</html>
```